High-end construction company needs a business card design

We need a modern looking business card that draws people in, is memorable and looks so good people will want to sick it on their fridges.
On the first side what is needed are:
Logo
My name - Tomasz Brelwik
Title - Managing Director
Website - www.varkelt.co.uk
Email - tomasz@varkelt.co.uk
Telephone - 020 5194 6281
Mobile - 07845139072
On the back side was is needed is a list of all the services we provide:
-Kitchen Renovations
-Bathroom Renovations
-House Renovations
-Garage Conversions
-Extensions
-Loft Conversions
-Conservatories
-Carpentry
-Tiling
-Electrical
-Plumbing & Heating
-Bricklaying
-Landscaping
-Decorating
-Plastering
We would like the colours to be the same shades as on the logo with grey or black for the words.
Target Market(s)
Anyone who needs building work done
Contact Information for Business Card
This business card is for a construction company which strives to deliver excellent service and quality.
The look and feel of the card should represent this.
Requirements
Must have
- On the first side what is needed are:
Logo
My name - Tomasz Brelwik
Title - Managing Director
Website - www.varkelt.co.uk
Email - tomasz@varkelt.co.uk
Telephone - 020 5194 6281
Mobile - 07845139072
Nice to have
- Cool looking features

```html
<!DOCTYPE html>
<html lang="en">
<head>
<meta charset="UTF-8">
<title>Varkelt Construction Ltd – Business Card</title>
<link href="https://fonts.googleapis.com/css2?family=Saira:wght@400;600;700&display=swap" rel="stylesheet">
<style>
  :root {
    --backdrop: #8a8a8a;
    --paper: #ffffff;
    --brand-green: #6abf45;
    --deep-green: #4a8f40;
    --ink-grey: #555555;
    --rule-grey: #d8d8d8;
    --on-green: #ffffff;
  }
  * { box-sizing: border-box; margin: 0; padding: 0; }
  html, body {
    width: 1125px; height: 1200px; overflow: hidden;
    background: var(--backdrop);
    font-family: "Saira", sans-serif;
  }
  .card {
    position: absolute;
    left: 162px;
    width: 800px; height: 457px;
  }
  .card--front { top: 110px; background: var(--paper); }
  .card--back  { top: 630px; background: var(--deep-green); }

  /* Front */
  .brand-name {
    position: absolute; right: 52px; top: 150px;
    text-align: right;
    color: var(--brand-green);
    font-weight: 700;
    line-height: 1;
  }
  .brand-name__main { display: block; font-size: 78px; letter-spacing: 1px; }
  .brand-name__sub  { display: block; font-size: 20px; letter-spacing: 3.2px; margin-top: 6px; }

  .name-accent {
    position: absolute; left: 0; top: 293px;
    width: 12px; height: 52px;
    background: var(--deep-green);
  }
  .person {
    position: absolute; left: 44px; top: 294px;
  }
  .person__name {
    font-size: 27px; font-weight: 700; color: var(--brand-green);
    line-height: 1.1; letter-spacing: 0.3px;
  }
  .person__title {
    font-size: 16px; font-weight: 400; color: var(--deep-green);
    line-height: 1.3;
  }

  .contact {
    position: absolute; top: 370px;
    list-style: none;
  }
  .contact li {
    display: flex; align-items: center;
    height: 24px;
    color: var(--ink-grey);
  }
  .contact svg { flex: none; fill: var(--brand-green); }
  .contact--phones { left: 44px; font-size: 17px; }
  .contact--phones svg { width: 16px; height: 16px; margin-right: 11px; }
  .contact--web { left: 248px; font-size: 15px; padding-left: 0; }
  .contact--web svg { width: 14px; height: 14px; margin-right: 12px; }
  .contact-divider {
    position: absolute; left: 230px; top: 370px;
    width: 1px; height: 48px; background: var(--rule-grey);
  }

  /* Back */
  .services {
    position: absolute; top: 126px;
    list-style: none;
  }
  .services--left  { left: 158px; }
  .services--right { left: 448px; }
  .services li {
    display: flex; align-items: center;
    height: 25px;
    font-size: 17px; color: var(--on-green);
    letter-spacing: 0.2px;
  }
  .services svg {
    width: 15px; height: 15px; margin-right: 11px; flex: none;
  }
</style>
</head>
<body>
<svg width="0" height="0" style="position:absolute">
  <defs>
    <symbol id="check-box" viewBox="0 0 16 16">
      <rect x="1" y="1" width="14" height="14" fill="none" stroke="#ffffff" stroke-width="2"/>
      <path d="M4 8.2 L7 11 L12.5 4.8" fill="none" stroke="#ffffff" stroke-width="2.2"/>
    </symbol>
  </defs>
</svg>

<section class="card card--front">
  <div class="brand-name">
    <span class="brand-name__main">VARKELT</span>
    <span class="brand-name__sub">CONSTRUCTION LTD</span>
  </div>

  <div class="name-accent"></div>
  <div class="person">
    <p class="person__name">TOMASZ BRELWIK</p>
    <p class="person__title">Managing Director</p>
  </div>

  <ul class="contact contact--phones">
    <li>
      <svg viewBox="0 0 16 16"><path d="M3.5 1 L6 1.5 L7 5 L5.3 6.4 C6.2 8.3 7.7 9.8 9.6 10.7 L11 9 L14.5 10 L15 12.5 C14.5 14 13 15 11.5 14.8 C6 14 2 10 1.2 4.5 C1 3 2 1.5 3.5 1 Z"/></svg>
      020 5194 6281
    </li>
    <li>
      <svg viewBox="0 0 16 16"><path d="M4 0.5 H12 A1.5 1.5 0 0 1 13.5 2 V14 A1.5 1.5 0 0 1 12 15.5 H4 A1.5 1.5 0 0 1 2.5 14 V2 A1.5 1.5 0 0 1 4 0.5 Z M4.3 2.5 V12 H11.7 V2.5 Z M8 12.8 A0.9 0.9 0 1 0 8 14.6 A0.9 0.9 0 1 0 8 12.8 Z"/></svg>
      07845139072
    </li>
  </ul>

  <div class="contact-divider"></div>

  <ul class="contact contact--web">
    <li>
      <svg viewBox="0 0 16 16"><path d="M1 3 H15 V13 H1 Z M2.5 4.5 L8 9 L13.5 4.5 Z"/></svg>
      tomasz@varkelt.co.uk
    </li>
    <li>
      <svg viewBox="0 0 16 16"><circle cx="8" cy="8" r="7.2"/><path d="M4 4.5 C6 5 6.5 7 5 8.5 C4.5 10 6 11 6.5 13 M10 2.5 C9 4 10.5 5.5 12 5.5 M10.5 9 C11.5 10 12.5 10.5 13 12" fill="none" stroke="#ffffff" stroke-width="1.2"/></svg>
      www.varkelt.co.uk
    </li>
  </ul>
</section>

<section class="card card--back">
  <ul class="services services--left">
    <li><svg viewBox="0 0 16 16"><use href="#check-box"/></svg>Kitchen Renovations</li>
    <li><svg viewBox="0 0 16 16"><use href="#check-box"/></svg>Bathroom Renovations</li>
    <li><svg viewBox="0 0 16 16"><use href="#check-box"/></svg>House Renovations</li>
    <li><svg viewBox="0 0 16 16"><use href="#check-box"/></svg>Garage Conversions</li>
    <li><svg viewBox="0 0 16 16"><use href="#check-box"/></svg>Extensions</li>
    <li><svg viewBox="0 0 16 16"><use href="#check-box"/></svg>Loft Conversions</li>
    <li><svg viewBox="0 0 16 16"><use href="#check-box"/></svg>Conservatories</li>
    <li><svg viewBox="0 0 16 16"><use href="#check-box"/></svg>Carpentry</li>
  </ul>
  <ul class="services services--right">
    <li><svg viewBox="0 0 16 16"><use href="#check-box"/></svg>Tiling</li>
    <li><svg viewBox="0 0 16 16"><use href="#check-box"/></svg>Electrical</li>
    <li><svg viewBox="0 0 16 16"><use href="#check-box"/></svg>Plumbing &amp; Heating</li>
    <li><svg viewBox="0 0 16 16"><use href="#check-box"/></svg>Bricklaying</li>
    <li><svg viewBox="0 0 16 16"><use href="#check-box"/></svg>Landscaping</li>
    <li><svg viewBox="0 0 16 16"><use href="#check-box"/></svg>Decorating</li>
    <li><svg viewBox="0 0 16 16"><use href="#check-box"/></svg>Plastering</li>
  </ul>
</section>
</body>
</html>
```